Real estate broker business card

Want a modern celan but effective business card for my residential and commercial real estate business. I want the back of the card to advertise my services and to capture business. I have attached the back of my current business card fore ideas
Updates

Logos, photo and text updates added! Added Saturday, September 3, 2016

Project Deadline Extended Reason: LOGOS, PHOTOS AND TEST JUST UPLOADED! I'M READY TO PICK A DESIGN! THANK YOU! Added Saturday, September 3, 2016

Target Market(s)

home buyers and seller. commercial buyers and sellers

Industry/Entity Type

Real Estate

Contact Information for Business Card

must have my contact information and my photo

Requirements
Must have
• Carla Ventrino
• Owner & Qualifying Broker
• Ventrino Real Estate Services
• 505.718.2094
• carla@ventrinohomes.example
• www.ventrinohomes.example
Nice to have
• metallic
• Business capture text: " Don't buy or lease property without someone looking out for your best interests. I will represent you on your home or investment purchase for FREE!"
• "Home owners, call today to receive a FREE market analysis for your homes value!

```html
<!DOCTYPE html>
<html lang="en">
<head>
<meta charset="utf-8">
<title>Ventrino Real Estate Services – Business Card</title>
<link href="https://fonts.googleapis.com/css2?family=Arimo:wght@400;700&display=swap" rel="stylesheet">
<style>
  :root {
    --backdrop: #4a403b;
    --card: #131517;
    --card-edge: #1c1f22;
    --teal: #1f8592;
    --silver: #9aa0a5;
    --white: #eef1f2;
    --muted: #b9bec2;
  }
  * { box-sizing: border-box; margin: 0; padding: 0; }
  html, body { width: 1200px; height: 864px; overflow: hidden; }
  body {
    background: var(--backdrop);
    font-family: "Arimo", Arial, sans-serif;
    display: flex;
    align-items: center;
    justify-content: center;
    gap: 40px;
  }
  .card {
    width: 540px;
    height: 309px;
    background: var(--card);
    border: 1px solid var(--card-edge);
    border-radius: 4px;
    box-shadow: 0 14px 30px rgba(0,0,0,.45);
    position: relative;
  }
  .brand {
    display: flex;
    align-items: center;
    gap: 12px;
    color: var(--teal);
    font-weight: 700;
    text-transform: uppercase;
  }
  .brand-dot {
    width: 34px; height: 34px;
    border-radius: 50%;
    background: var(--teal);
    flex: none;
  }
  .brand-name { line-height: 1.1; }
  .brand-name .big { display: block; font-size: 34px; letter-spacing: 2px; }
  .brand-name .small { display: block; font-size: 12px; letter-spacing: 3.4px; }

  /* back of card */
  .card-back {
    display: flex;
    flex-direction: column;
    align-items: center;
    justify-content: center;
    gap: 34px;
  }
  .pitch {
    color: var(--muted);
    font-size: 13px;
    line-height: 1.5;
    text-align: center;
    max-width: 420px;
  }

  /* front of card */
  .card-front {
    display: flex;
    align-items: center;
  }
  .front-brand {
    width: 270px;
    display: flex;
    justify-content: center;
  }
  .front-brand .brand-name .big { font-size: 28px; }
  .front-brand .brand-name .small { font-size: 10px; letter-spacing: 2.6px; }
  .divider {
    width: 1px;
    height: 170px;
    background: linear-gradient(var(--card), var(--silver), var(--card));
  }
  .contact {
    padding-left: 24px;
    color: var(--white);
    font-size: 14px;
  }
  .contact-name { color: var(--teal); font-size: 19px; font-weight: 700; margin-bottom: 4px; }
  .contact-title { line-height: 1.35; margin-bottom: 12px; }
  .contact-list { list-style: none; }
  .contact-list li { display: flex; align-items: center; gap: 9px; line-height: 1.7; }
  .contact-list svg { width: 13px; height: 13px; flex: none; fill: var(--teal); }
</style>
</head>
<body>

<section class="card card-back" aria-label="Back of card">
  <div class="brand">
    <span class="brand-dot"></span>
    <span class="brand-name"><span class="big">Ventrino</span><span class="small">Real Estate Services</span></span>
  </div>
  <p class="pitch">Don't buy or lease property without someone looking out for your best interests.<br>I will represent you on your home or investment purchase for FREE!</p>
</section>

<section class="card card-front" aria-label="Front of card">
  <div class="front-brand">
    <div class="brand">
      <span class="brand-dot"></span>
      <span class="brand-name"><span class="big">Ventrino</span><span class="small">Real Estate Services</span></span>
    </div>
  </div>
  <div class="divider"></div>
  <div class="contact">
    <p class="contact-name">Carla Ventrino</p>
    <p class="contact-title">Owner &amp; Qualifying Broker<br>Ventrino Real Estate Services</p>
    <ul class="contact-list">
      <li><svg viewBox="0 0 16 16" aria-hidden="true"><path d="M3.6 1.2l2.3 2.6-1.3 1.9c.9 2 2.6 3.7 4.6 4.6l1.9-1.3 2.6 2.3-1.4 2.6C7.2 13.6 2.4 8.8 1.1 3.5z"/></svg>505.718.2094</li>
      <li><svg viewBox="0 0 16 16" aria-hidden="true"><path d="M1 3h14v10H1z M1.6 3.4L8 8.6l6.4-5.2" stroke="#131517" stroke-width="1.2"/></svg>carla@ventrinohomes.example</li>
      <li><svg viewBox="0 0 16 16" aria-hidden="true"><circle cx="8" cy="8" r="7"/><path d="M1 8h14M8 1c-3 3.5-3 10.5 0 14M8 1c3 3.5 3 10.5 0 14" stroke="#131517" stroke-width="1" fill="none"/></svg>www.ventrinohomes.example</li>
    </ul>
  </div>
</section>

</body>
</html>
```